Heron Property Inspection business card

I am the principal inspector of Heron Property Inspections. I serve Northern Virginia from Winchester to Arlington.Associate, Federated Guild of Dwelling Examiners (FGDE)Graduate, FGDE Home Inspectors CourseNational Association of Home Inspectors ExamI'd like the business card to look more professional than comical.I pulled the attached picture off the web. I'd like to have something like that or an image of a house as my logo on the cards.

Target Market(s)

Persons who recently purchased a home.

Industry/Entity Type

Business

Contact Information for Business Card

Bob AllenBadger Home Inspections, LLC.4455 River RoadBluemont, Virginia 20135cell: 703-231-6680e-mail: tkmarlow@postvale.net

Font styles to use
Serif
Sans Serif

Requirements
Must have
• I'd like to have a logo, something that identifies me as a home inspector. The attached images are something that I'd like to have incorporated into my business card logo.
Nice to have
• I'd like a sketch of a house and/or a magnifying glass showing a house being inspected. The attached images are used as a suggestion only, I do not own the images.
Should not have
• Gimmicky stuff. I want to appear professional and trustworthy.

```html
<!DOCTYPE html>
<html lang="en">
<head>
<meta charset="utf-8">
<title>Heron Property Inspections – Business Card</title>
<link rel="stylesheet" href="https://fonts.googleapis.com/css2?family=Open+Sans:wght@400;600;700&display=swap">
<style>
  :root {
    --page: #ebe7e1;
    --card: #ffffff;
    --red: #b5161f;
    --red-deep: #8a0d15;
    --ink: #3d3d3f;
    --grey: #6b6b6d;
    --rule: #c9323a;
  }
  * { margin: 0; padding: 0; box-sizing: border-box; }
  html, body {
    width: 1200px; height: 818px; overflow: hidden;
    background: var(--page);
    font-family: "Open Sans", Arial, sans-serif;
  }
  .stage {
    width: 1200px; height: 818px;
    display: flex; align-items: center; justify-content: center;
  }
  .card {
    position: relative;
    width: 900px; height: 514px;
    background: var(--card);
    border-radius: 18px;
    overflow: hidden;
    box-shadow: 0 10px 30px rgba(0,0,0,.18);
    display: flex; flex-direction: column;
  }
  .band {
    height: 92px;
    background: linear-gradient(180deg, var(--red) 0%, var(--red-deep) 100%);
    color: #fff;
    display: flex; align-items: center;
    padding: 0 40px;
  }
  .band--top { font-weight: 700; font-size: 34px; letter-spacing: .2px; }
  .band--bottom { font-weight: 600; font-size: 24px; justify-content: flex-end; }
  .body {
    flex: 1;
    display: flex; align-items: center;
    padding: 0 40px;
  }
  .brand {
    width: 47%;
    display: flex; align-items: center; gap: 16px;
  }
  .brand__mark {
    width: 22px; height: 22px; flex: none;
    background: var(--red);
  }
  .brand__name {
    color: var(--grey);
    font-weight: 600;
    font-size: 30px;
    line-height: 1.2;
  }
  .divider {
    width: 1px; height: 230px;
    background: linear-gradient(180deg, transparent, var(--rule) 30%, var(--rule) 70%, transparent);
    margin: 0 44px 0 10px;
  }
  .person { flex: 1; }
  .person__name { font-weight: 700; font-size: 36px; color: var(--ink); line-height: 1.15; }
  .person__title { font-size: 22px; color: var(--red); margin-bottom: 26px; }
  .contact { list-style: none; }
  .contact li {
    display: flex; align-items: center; gap: 10px;
    font-size: 20px; color: var(--ink); line-height: 1.6;
  }
  .contact svg { width: 20px; height: 20px; flex: none; }
</style>
</head>
<body>
<main class="stage">
  <article class="card">
    <header class="band band--top">Tim MarlowHeron Property Inspections, LLC</header>
    <section class="body">
      <div class="brand">
        <span class="brand__mark"></span>
        <p class="brand__name">Tim MarlowHeron<br>Property Inspections, LLC</p>
      </div>
      <div class="divider"></div>
      <div class="person">
        <h1 class="person__name">Employee Name</h1>
        <p class="person__title">Managing Director</p>
        <ul class="contact">
          <li>
            <svg viewBox="0 0 20 20" aria-hidden="true"><rect width="20" height="20" rx="3" fill="#b5161f"/><rect x="6.5" y="3.5" width="7" height="13" rx="1.2" fill="none" stroke="#fff" stroke-width="1.4"/><circle cx="10" cy="14" r=".9" fill="#fff"/></svg>
            703-555-0192
          </li>
          <li>
            <svg viewBox="0 0 20 20" aria-hidden="true"><rect width="20" height="20" rx="3" fill="#b5161f"/><rect x="4" y="6" width="12" height="8.5" fill="none" stroke="#fff" stroke-width="1.4"/><path d="M4 6l6 5 6-5" fill="none" stroke="#fff" stroke-width="1.4"/></svg>
            tkmarlow@postvale.net
          </li>
        </ul>
      </div>
    </section>
    <footer class="band band--bottom">7182 Quarry LaneFernhill, Virginia 20148</footer>
  </article>
</main>
</body>
</html>
```